Business card por a urban DJ, up scale audience target

Need a sober design, modern, conservative colors but i can consider some options, y play rnb, hip hop, EDM and top40.

Business card for contact and personal info, double sided, use logo attrached please; im 42 so i need a card acording to my age an target audience.

Target Market(s)

Adult people, up scale audience

Industry/Entity Type

Music Download

Contact Information for Business Card

Cel (318) 4207265518 www.lumadrift.com

Requirements
Must have
• open mind
Nice to have
• open mind
Should not have
• DJ

```html
<!DOCTYPE html>
<html lang="en">
<head>
<meta charset="utf-8">
<title>Lumadrift business card – front and back</title>
<link href="https://fonts.googleapis.com/css2?family=Open+Sans:wght@400;600;800&display=swap" rel="stylesheet">
<style>
  :root {
    --page: #e9e7e3;
    --paper: #f1f1f1;
    --paper-shade: #dcdcdc;
    --ink: #2b2b2b;
    --ink-deep: #232323;
    --light-text: #f4f4f4;
    --muted-text: #d6d6d6;
  }
  * { box-sizing: border-box; margin: 0; padding: 0; }
  html, body {
    width: 1200px; height: 780px; overflow: hidden;
    background: var(--page);
    font-family: "Open Sans", Arial, sans-serif;
  }
  .stage { position: relative; width: 1200px; height: 780px; }

  .card {
    position: absolute;
    width: 560px; height: 320px;
    border-radius: 6px;
    overflow: hidden;
    box-shadow: 0 14px 30px rgba(0,0,0,.18), 0 2px 5px rgba(0,0,0,.12);
  }

  /* Front */
  .card-front {
    left: 60px; top: 70px;
    background: linear-gradient(135deg, #fafafa 0%, var(--paper) 55%, var(--paper-shade) 100%);
  }
  .contact-panel {
    position: absolute; right: 24px; top: 0;
    width: 300px; height: 186px;
    background: var(--ink);
    border-radius: 0 0 14px 14px;
    padding: 30px 26px 0 30px;
    color: var(--light-text);
  }
  .person-name { font-weight: 600; font-size: 20px; letter-spacing: .2px; line-height: 1.1; }
  .person-role { font-weight: 400; font-size: 14px; color: var(--muted-text); margin-top: 2px; }
  .contact-list { list-style: none; margin-top: 28px; }
  .contact-list li {
    display: flex; align-items: center; gap: 8px;
    font-size: 14px; line-height: 22px;
  }
  .contact-icon {
    width: 14px; height: 14px; flex: none;
    background: var(--light-text); border-radius: 2px;
    display: flex; align-items: center; justify-content: center;
  }
  .contact-icon svg { width: 10px; height: 10px; }

  .side-tab {
    position: absolute; left: -14px; bottom: 30px;
    width: 60px; height: 150px;
    background: var(--ink);
    border-radius: 14px;
  }
  .brand {
    position: absolute; display: flex; align-items: center; gap: 12px;
    font-weight: 800; letter-spacing: 2px; line-height: 1;
  }
  .brand-mark { display: block; flex: none; }
  .card-front .brand {
    left: 78px; bottom: 40px;
    font-size: 76px; color: var(--ink);
  }
  .card-front .brand-mark { width: 18px; height: 18px; background: var(--ink); }

  /* Back */
  .card-back {
    right: 60px; bottom: 70px;
    background: linear-gradient(135deg, #333 0%, var(--ink) 50%, var(--ink-deep) 100%);
  }
  .end-tab {
    position: absolute; top: 50%; transform: translateY(-50%);
    width: 54px; height: 170px;
    background: var(--paper);
    border-radius: 14px;
  }
  .end-tab-left { left: -20px; }
  .end-tab-right { right: -20px; }
  .card-back .brand {
    left: 50%; top: 50%; transform: translate(-50%, -50%);
    font-size: 84px; color: var(--light-text);
  }
  .card-back .brand-mark { width: 20px; height: 20px; background: var(--light-text); }
</style>
</head>
<body>
<main class="stage">

  <section class="card card-front" aria-label="Card front">
    <div class="contact-panel">
      <p class="person-name">EMPLOYEE NAME</p>
      <p class="person-role">Development Manager</p>
      <ul class="contact-list">
        <li>
          <span class="contact-icon">
            <svg viewBox="0 0 10 10"><rect x="2.5" y="0.5" width="5" height="9" rx="1" fill="none" stroke="#2b2b2b" stroke-width="1.2"/><rect x="4" y="7.4" width="2" height="0.9" fill="#2b2b2b"/></svg>
          </span>
          (318) 4207265518
        </li>
        <li>
          <span class="contact-icon">
            <svg viewBox="0 0 10 10"><rect x="0.8" y="2" width="8.4" height="6" fill="none" stroke="#2b2b2b" stroke-width="1.1"/><path d="M0.8 2 L5 5.6 L9.2 2" fill="none" stroke="#2b2b2b" stroke-width="1.1"/></svg>
          </span>
          hello@lumadrift.com
        </li>
        <li>
          <span class="contact-icon">
            <svg viewBox="0 0 10 10"><circle cx="5" cy="5" r="4" fill="none" stroke="#2b2b2b" stroke-width="1.1"/><ellipse cx="5" cy="5" rx="1.8" ry="4" fill="none" stroke="#2b2b2b" stroke-width="0.9"/><path d="M1 5 H9" stroke="#2b2b2b" stroke-width="0.9"/></svg>
          </span>
          www.lumadrift.com
        </li>
      </ul>
    </div>
    <div class="side-tab"></div>
    <div class="brand"><span class="brand-mark"></span>LUMA</div>
  </section>

  <section class="card card-back" aria-label="Card back">
    <div class="end-tab end-tab-left"></div>
    <div class="end-tab end-tab-right"></div>
    <div class="brand"><span class="brand-mark"></span>LUMA</div>
  </section>

</main>
</body>
</html>
```